Dunmore Roofing

Want a professional looking business card

Industry/Entity Type

Business

Contact Information for Business Card

Paul Dunmore ( Owner) paul@dunmoreroofing-example.com, www.dunmoreroofing-example.com, Adress: 4172 Township road 43 Lakeview,ON K9X4T2

```html
<!DOCTYPE html>
<html lang="en">
<head>
<meta charset="utf-8">
<title>Dunmore Roofing — Business Card</title>
<link rel="stylesheet" href="https://fonts.googleapis.com/css2?family=Roboto:wght@400;700;900&family=Roboto+Condensed:wght@500&display=swap">
<style>
  :root {
    --bg: #e9e6e2;
    --card-white: #f3f3f3;
    --brand-blue: #1b4587;
    --rule-grey: #7d7d7d;
    --ink-white: #ffffff;
    --shadow: rgba(0, 0, 0, 0.35);
  }
  * { margin: 0; padding: 0; box-sizing: border-box; }
  html, body { width: 1200px; height: 960px; overflow: hidden; }
  body {
    background: var(--bg);
    position: relative;
    font-family: "Roboto", Arial, sans-serif;
  }
  .card {
    position: absolute;
    width: 600px;
    height: 342px;
    box-shadow: 0 4px 10px var(--shadow);
    overflow: hidden;
  }
  /* Front */
  .card-front { left: 314px; top: 123px; background: var(--brand-blue); }
  .front-head {
    position: absolute; left: 0; top: 0; width: 600px; height: 197px;
    background: var(--card-white);
  }
  .front-divider { position: absolute; left: 0; top: 192px; }
  .wordmark {
    position: absolute; left: 0; width: 100%; top: 116px;
    text-align: center; color: var(--brand-blue);
    font-weight: 900; font-size: 31px; letter-spacing: 3px; line-height: 1;
  }
  .wordmark .sub {
    display: block; margin-top: 6px;
    font-size: 14px; letter-spacing: 20px; padding-left: 20px;
  }
  .contact {
    position: absolute; left: 28px; top: 229px;
    color: var(--ink-white); font-size: 14.5px; line-height: 18px;
  }
  .contact .address { margin-bottom: 10px; }
  .contact .line { display: flex; align-items: center; gap: 8px; height: 20px; }
  .contact svg { width: 13px; height: 13px; flex: none; }
  .person {
    position: absolute; right: 28px; top: 244px;
    text-align: right; color: var(--ink-white);
  }
  .person .name {
    font-family: "Roboto Condensed", "Arial Narrow", sans-serif;
    font-weight: 500; font-size: 23px; line-height: 1; margin-bottom: 9px;
  }
  .person .role { font-size: 15px; line-height: 20px; }
  .person .email { font-size: 14.5px; line-height: 18px; }
  /* Back */
  .card-back { left: 312px; top: 482px; height: 343px; background: var(--brand-blue); }
  .back-wordmark {
    position: absolute; left: 0; width: 100%; top: 135px;
    text-align: center; color: var(--ink-white);
    font-weight: 900; font-size: 34px; letter-spacing: 3px; line-height: 1;
  }
  .back-wordmark .sub {
    display: block; margin-top: 5px;
    font-size: 15px; letter-spacing: 22px; padding-left: 22px;
  }
  .back-url {
    position: absolute; left: 0; width: 100%; top: 193px;
    text-align: center; color: var(--ink-white);
    font-size: 14px; letter-spacing: 2px;
  }
</style>
</head>
<body>

  <section class="card card-front">
    <div class="front-head">
      <div class="wordmark">DUNMORE<span class="sub">ROOFING</span></div>
    </div>
    <svg class="front-divider" width="600" height="20" viewBox="0 0 600 20">
      <polygon points="0,5 530,5 543,18 556,5 600,5 600,20 0,20" fill="var(--brand-blue)"/>
      <polyline points="0,4 530,4 543,16 556,4 600,4" fill="none" stroke="var(--rule-grey)" stroke-width="3"/>
    </svg>
    <div class="contact">
      <p class="address">4172 Township road 43<br>Lakeview, ON K9X4T2</p>
      <p class="line">
        <svg viewBox="0 0 24 24"><path fill="#fff" d="M6.6 10.8a15 15 0 0 0 6.6 6.6l2.2-2.2c.3-.3.7-.4 1-.2 1.1.4 2.3.6 3.6.6.6 0 1 .4 1 1V20c0 .6-.4 1-1 1A17 17 0 0 1 3 4c0-.6.4-1 1-1h3.5c.6 0 1 .4 1 1 0 1.3.2 2.5.6 3.6.1.3 0 .7-.2 1z"/></svg>
        613 555 0147
      </p>
      <p class="line">
        <svg viewBox="0 0 24 24"><circle cx="12" cy="12" r="10" fill="#fff"/><path d="M12 2a15 15 0 0 1 0 20M12 2a15 15 0 0 0 0 20M2 12h20" stroke="var(--brand-blue)" stroke-width="1.6" fill="none"/></svg>
        www.dunmoreroofing-example.com
      </p>
    </div>
    <div class="person">
      <p class="name">PAUL DUNMORE</p>
      <p class="role">OWNER</p>
      <p class="email">paul@dunmoreroofing-example.com</p>
    </div>
  </section>

  <section class="card card-back">
    <div class="back-wordmark">DUNMORE<span class="sub">ROOFING</span></div>
    <p class="back-url">www.dunmoreroofing-example.com</p>
  </section>

</body>
</html>
```